Business Name: DM Space Arranging Pty Ltd

Business Type: Professional Home Styling and Minor Renovation Business

Logo: Attached is the logo that has been created.
I always envisaged the logo in the middle of the business card with my full name underneath it.

Marnie Tulloch B.Com LMR HTV
Property Stylist & Project Manager

Include dot points of services
Staging Houses for Sale
Minor Home Renovations
Home Styling & Project Management
Re-Designing Living Spaces to Aid the Disabled

Somewhere on the card I would like to incorporate
"Property Styling and Cosmetic Renovations"

Colour Scheme:
Gloss black business card, with white and then
Gold or Silver as the highlight colours.

Incorporate a small amount of yellow only if possible to make it pop. If this really doesn’t work it doesn’t have to be used. Also l like the colour teal if that needs to be used as a contrast colour.

Feel/Themes
• I love antique chairs, regal expensive looking furniture mixed with modern homes (this is the unique style I want to sell) antique and modern mix that looks high class as well as modern and fresh, targeting an executive market.
• I want to use an orchid as a trademark throughout the course of my work, not sure if this can somehow be incorporated? Also really like crowns to give that regal/antique feel and then something else to give that modern twist (I don’t know what the something else could be)
• Wall Paper Look (on a portion of it not all of it, like a French look)
• Overall feel - A very deluxe and professional feel with a little bit of creative flare.

I hope this helps create a bit of a picture.

Is it ok that I call you tomorrow morning? My mobile number is 0438 926 574 if you have any questions for me in the meantime.

Target Market(s)

High Quality Executive Market - People selling homes

Industry/Entity Type

Business

Contact Information for Business Card

Include dot points of services:
Staging Houses for Sale
Minor Home Renovations

Font styles to use
Serif
Script

Colors
33b8a4
fbed22

Requirements
Must have
• Marnie Tulloch B.Com LMR HTV
• Property Stylist & Project Manager
• LMR and HTV Logos on the card
• "Dramatically increase the value of your property"
Nice to have
• Colour Scheme:
• Gloss black business card, with white and then
• Gold or Silver as the highlight colours.
• Incorporate a small amount of yellow only if possible to make it pop. If this really doesn’t work it doesn’t have to be used. Also l like the colour teal if that needs to be used as a contrast colour.
• Also like teal as a highlight colour.

```html
<!DOCTYPE html>
<html lang="en">
<head>
<meta charset="utf-8">
<title>DM Space Arranging Pty Ltd – Business Cards</title>
<link rel="stylesheet" href="https://fonts.googleapis.com/css2?family=Pinyon+Script&family=Tinos:wght@400&family=Roboto+Condensed:wght@400&display=swap">
<style>
  :root {
    --backdrop: #1c1c1e;
    --card-white: #ffffff;
    --gloss-black: #0b0b0c;
    --gloss-black-hi: #2a2a2c;
    --gold: #c9a13b;
    --gold-light: #e8c766;
    --silver: #a9a9ab;
    --silver-light: #d8d8da;
    --text-grey: #9a9a9c;
    --ink: #2b2b2b;
  }
  * { margin: 0; padding: 0; box-sizing: border-box; }
  html, body {
    width: 1200px; height: 852px; overflow: hidden;
    background: var(--backdrop);
  }
  .stage {
    position: relative; width: 1200px; height: 852px;
    display: flex; align-items: center; justify-content: center; gap: 40px;
  }
  .card {
    position: relative; width: 520px; height: 297px;
    border-radius: 12px; overflow: hidden;
    background: var(--card-white);
    box-shadow: 0 18px 40px rgba(0,0,0,.55);
  }
  .card__art { position: absolute; inset: 0; }

  .brand { position: absolute; left: 0; right: 0; text-align: center; }
  .brand__ornament {
    position: absolute; border-radius: 50%;
    background: radial-gradient(ellipse at center, rgba(190,190,192,.45) 0%, rgba(220,220,222,.25) 55%, rgba(255,255,255,0) 75%);
  }
  .brand__name {
    position: relative;
    font-family: "Tinos", serif; font-size: 15px; letter-spacing: 3.2px;
    text-transform: uppercase; color: var(--ink);
  }

  /* front */
  .card--front .brand { top: 0; height: 172px; }
  .card--front .brand__ornament { left: 150px; top: 22px; width: 220px; height: 130px; }
  .card--front .brand__name { top: 82px; }
  .card--front .band {
    position: absolute; left: 0; right: 0; top: 172px; bottom: 0;
    background: linear-gradient(160deg, var(--gloss-black-hi) 0%, var(--gloss-black) 45%, #000 100%);
  }
  .person {
    position: absolute; left: 0; right: 0; top: 180px; text-align: center;
  }
  .person__name {
    font-family: "Pinyon Script", cursive; font-size: 34px; line-height: 1.1;
    color: var(--gold);
  }
  .person__credentials, .person__title {
    font-family: "Tinos", serif; font-size: 15px; line-height: 1.35;
    color: var(--text-grey);
  }

  /* back */
  .card--back .brand { top: 0; left: 60px; right: 200px; height: 130px; }
  .card--back .brand__ornament { left: 60px; top: 20px; width: 140px; height: 100px; }
  .card--back .brand__name { top: 64px; font-size: 13px; letter-spacing: 2.6px; }
  .tagline {
    position: absolute; right: 20px; top: 122px; text-align: right;
    font-family: "Roboto Condensed", sans-serif; font-size: 15px; line-height: 1.3;
    color: var(--gold-light);
  }
  .services {
    position: absolute; left: 22px; top: 214px; list-style: none;
    font-family: "Tinos", serif; font-size: 14px; line-height: 19px;
    color: #f2f2f2;
  }
  .services li::before { content: "»"; margin-right: 9px; color: #f2f2f2; }
</style>
</head>
<body>
<main class="stage">

  <article class="card card--front">
    <div class="band"></div>
    <div class="brand">
      <div class="brand__ornament" role="img" aria-label="Faint silver flourish and crown ornament behind the company name"></div>
      <p class="brand__name">DM Space Arranging Pty Ltd</p>
    </div>
    <div class="person">
      <p class="person__name">Marnie Tulloch</p>
      <p class="person__credentials">B.Com LMR HTV</p>
      <p class="person__title">Property Stylist &amp; Project Manager</p>
    </div>
  </article>

  <article class="card card--back">
    <svg class="card__art" width="520" height="297" viewBox="0 0 520 297" aria-hidden="true">
      <defs>
        <linearGradient id="gloss" x1="0" y1="0" x2="1" y2="1">
          <stop offset="0" stop-color="#2a2a2c"/>
          <stop offset=".45" stop-color="#0b0b0c"/>
          <stop offset="1" stop-color="#000"/>
        </linearGradient>
        <linearGradient id="goldline" x1="0" y1="0" x2="1" y2="0">
          <stop offset="0" stop-color="#b8862a"/>
          <stop offset=".5" stop-color="#f1d27a"/>
          <stop offset="1" stop-color="#b8862a"/>
        </linearGradient>
      </defs>
      <polygon points="0,200 520,72 520,297 0,297" fill="url(#gloss)"/>
      <line x1="0" y1="198" x2="520" y2="70" stroke="url(#goldline)" stroke-width="3"/>
    </svg>
    <div class="brand">
      <div class="brand__ornament" role="img" aria-label="Faint silver flourish and crown ornament behind the company name"></div>
      <p class="brand__name">DM Space Arranging Pty Ltd</p>
    </div>
    <p class="tagline">Property Styling &amp;<br>Cosmetic Renovations</p>
    <ul class="services">
      <li>Staging Houses for Sale</li>
      <li>Minor Home Renovations</li>
      <li>Home Styling &amp; Project Management</li>
      <li>Re-Designing Living Spaces to Aid the Disabled</li>
    </ul>
  </article>

</main>
</body>
</html>
```